Business Card Design

We provide services doing multiple jobs in the construction industry.Please note: The company name needs to be ROCK SOLID BUILDING SERVICESAttached logo was an example of what we wanted. Can you change up the colors?

Industry/Entity Type

Construction

Contact Information for Business Card

ROCK SOLID BUILDING SERVICES5401 HUDSON BEND RDAUSTIN, TX 78734(512)243-6854ROCKSOLIDBUILDINGSERVICES@GMAIL.COM

```html
<!DOCTYPE html>
<html lang="en">
<head>
<meta charset="utf-8">
<title>Pearlwood Framing Works – Business Card</title>
<link rel="stylesheet" href="https://fonts.googleapis.com/css2?family=Arimo:wght@400;700&family=Tinos:wght@400;700&display=swap">
<style>
  :root {
    --backdrop: #d9d9d6;
    --card-white: #ffffff;
    --ink: #111111;
    --navy-deep: #1f2361;
    --navy-light: #2f3585;
    --band-black: #050505;
    --name-cream: #ece5d3;
    --rule-white: #ffffff;
  }
  * { margin: 0; padding: 0; box-sizing: border-box; }
  html, body {
    width: 1200px; height: 817px; overflow: hidden;
    background: var(--backdrop);
  }
  .canvas {
    width: 1200px; height: 817px;
    display: flex; align-items: center; justify-content: center;
  }
  .card {
    position: relative;
    width: 1050px; height: 600px;
    background: var(--card-white);
    overflow: hidden;
    box-shadow: 0 6px 24px rgba(0,0,0,.18);
  }
  .brand {
    position: absolute; top: 70px; left: 0; width: 100%;
    display: flex; align-items: center; justify-content: center; gap: 16px;
  }
  .brand-square {
    width: 34px; height: 34px; background: var(--navy-deep);
  }
  .brand-name {
    font-family: "Arimo", sans-serif; font-weight: 700;
    font-size: 34px; letter-spacing: 2px; color: var(--navy-deep);
  }
  .contact {
    position: absolute; top: 176px; left: 0; width: 100%;
    text-align: center;
    font-family: "Arimo", sans-serif; font-size: 27px;
    line-height: 46px; color: var(--ink);
  }
  .contact p { margin: 0; }
  .lower-field {
    position: absolute; left: 0; right: 0; bottom: 0; height: 252px;
    background: var(--band-black);
  }
  .name-band {
    position: absolute; left: 0; top: 0; right: 56px; height: 142px;
    background: linear-gradient(90deg, var(--navy-deep), var(--navy-light));
    border-top-right-radius: 42px;
    border-top: 3px solid var(--rule-white);
    border-right: 3px solid var(--rule-white);
    display: flex; align-items: center; justify-content: center;
  }
  .company-name {
    font-family: "Tinos", serif; font-size: 46px; letter-spacing: 2px;
    color: var(--name-cream);
  }
</style>
</head>
<body>
  <main class="canvas">
    <article class="card">
      <div class="brand">
        <span class="brand-square"></span>
        <span class="brand-name">PEARLWOOD FRAMING</span>
      </div>
      <div class="contact">
        <p>7732 FERNGLEN PASS LN AUSTIN, TX 78734</p>
        <p>(512)555-0193</p>
        <p>PEARLWOODFRAMINGWORKS@MAILNEST.EXAMPLE</p>
      </div>
      <div class="lower-field">
        <div class="name-band">
          <h1 class="company-name">PEARLWOOD FRAMING WORKS</h1>
        </div>
      </div>
    </article>
  </main>
</body>
</html>
```